Weightloss company needs Business Card

We want a business card that is clean and professional, yet portrays that we are a friendly, innovative, and versatile program designed to fit the needs of our clients.
I would like there to be 2 sides, one side having an appointment card, and the other side containing the logo and business information. There can be decorations on both sides. The logo is attached.

Target Market(s)

Men and women 40-60

Industry/Entity Type

Business

Contact Information for Business Card

Font styles to use
Sans Serif

Requirements
Must have
• The logo, space for business information
Nice to have
• The colors in the logo
Should not have
• No pictures of people or food

```html
<!DOCTYPE html>
<html lang="en">
<head>
<meta charset="utf-8">
<title>Turnaround Wellness – Business Card</title>
<link rel="stylesheet" href="https://fonts.googleapis.com/css2?family=Source+Sans+3:wght@400;600;700&display=swap">
<style>
  :root {
    --brand-red: #ff0033;
    --card-white: #ffffff;
    --ink: #111111;
    --backdrop: #ece9e6;
    --divider: rgba(255, 255, 255, 0.35);
  }
  * { box-sizing: border-box; margin: 0; padding: 0; }
  html, body { width: 1200px; height: 900px; overflow: hidden; }
  body {
    position: relative;
    background: var(--backdrop);
    font-family: "Source Sans 3", "Myriad Pro", Arial, sans-serif;
  }

  .card { position: absolute; overflow: hidden; background: var(--card-white); box-shadow: 0 6px 18px rgba(0,0,0,0.15); }

  /* Front */
  .card--front { left: 77px; top: 34px; width: 589px; height: 364px; }
  .front__brand { position: absolute; left: 0; top: 0; width: 100%; height: 182px; display: flex; align-items: center; padding-left: 32px; gap: 14px; }
  .brand__dot { width: 22px; height: 22px; border-radius: 50%; background: var(--brand-red); }
  .brand__name { font-size: 34px; font-weight: 700; color: var(--brand-red); letter-spacing: -0.3px; }
  .front__info { position: absolute; left: 0; top: 182px; width: 100%; height: 182px; background: var(--brand-red); color: var(--card-white); }
  .person__name { position: absolute; left: 31px; top: 8px; font-size: 22px; font-weight: 700; line-height: 30px; }
  .person__role { position: absolute; left: 31px; top: 35px; font-size: 16px; line-height: 22px; }
  .contact-list { position: absolute; left: 0; top: 73px; width: 248px; list-style: none; }
  .contact-item { display: flex; align-items: center; height: 31px; padding-left: 33px; font-size: 16px; border-top: 1px solid var(--divider); }
  .contact-item:first-child { border-top: none; }
  .contact-item svg { width: 12px; height: 12px; margin-right: 13px; fill: var(--card-white); flex: none; }

  /* Back */
  .card--back { left: 388px; top: 505px; width: 567px; height: 352px; }
  .back__header { position: absolute; left: 0; top: 0; width: 100%; height: 106px; padding-top: 10px; background: var(--brand-red); color: var(--card-white); display: flex; align-items: center; justify-content: center; font-size: 21px; font-weight: 600; letter-spacing: 0.2px; }
  .appointment-form { position: absolute; left: 101px; top: 146px; width: 365px; }
  .form-row { display: flex; align-items: baseline; height: 43px; font-size: 15px; font-weight: 700; color: var(--brand-red); }
  .form-label { margin-right: 4px; }
  .form-line { flex: 1; border-bottom: 2px dotted var(--ink); height: 10px; }
  .form-unit { color: var(--ink); font-weight: 600; font-size: 15px; margin: 0 1px; }
  .back__footer { position: absolute; left: 0; top: 264px; width: 100%; height: 88px; background: var(--brand-red); color: var(--card-white); display: flex; flex-direction: column; align-items: center; justify-content: center; font-size: 17px; font-weight: 600; line-height: 23px; text-align: center; }
</style>
</head>
<body>
  <section class="card card--front">
    <div class="front__brand">
      <span class="brand__dot"></span>
      <span class="brand__name">Turnaround Wellness</span>
    </div>
    <div class="front__info">
      <p class="person__name">Daniel Harper</p>
      <p class="person__role">Managing Director</p>
      <ul class="contact-list">
        <li class="contact-item">
          <svg viewBox="0 0 24 24"><path d="M6.6 10.8a15.1 15.1 0 0 0 6.6 6.6l2.2-2.2a1 1 0 0 1 1-.25 11.4 11.4 0 0 0 3.6.57 1 1 0 0 1 1 1V20a1 1 0 0 1-1 1A17 17 0 0 1 3 4a1 1 0 0 1 1-1h3.5a1 1 0 0 1 1 1c0 1.25.2 2.45.57 3.57a1 1 0 0 1-.25 1z"/></svg>
          044-987 654 321
        </li>
        <li class="contact-item">
          <svg viewBox="0 0 24 24"><path d="M2 5h20v14H2z M2 5l10 8 10-8" /></svg>
          hello@turnaround.com
        </li>
        <li class="contact-item">
          <svg viewBox="0 0 24 24"><path d="M10.6 13.4a1 1 0 0 1 0-1.4l4-4a1 1 0 1 1 1.4 1.4l-4 4a1 1 0 0 1-1.4 0zM8.5 20a4.5 4.5 0 0 1-3.2-7.7l2.5-2.5 1.4 1.4-2.5 2.5a2.5 2.5 0 0 0 3.6 3.6l2.5-2.5 1.4 1.4-2.5 2.5A4.5 4.5 0 0 1 8.5 20zm8.4-5.8-1.4-1.4 2.5-2.5a2.5 2.5 0 0 0-3.6-3.6l-2.5 2.5-1.4-1.4 2.5-2.5a4.5 4.5 0 0 1 6.4 6.4z"/></svg>
          www.turnaround.com
        </li>
      </ul>
    </div>
  </section>

  <section class="card card--back">
    <div class="back__header">YOUR NEXT APPOINTMENT IS</div>
    <div class="appointment-form">
      <div class="form-row"><span class="form-label">Name:</span><span class="form-line"></span></div>
      <div class="form-row"><span class="form-label">Date:</span><span class="form-line"></span></div>
      <div class="form-row"><span class="form-label">Time:</span><span class="form-line"></span><span class="form-unit">AM</span><span class="form-line"></span><span class="form-unit">PM</span></div>
    </div>
    <div class="back__footer">
      <span>IF UNABLE TO KEEP APPOINTMENT,</span>
      <span>KINDLY GIVE 24HRS NOTICE.</span>
    </div>
  </section>
</body>
</html>
```